Business Card Design Project

We are a construction company in Orange County, CA. We need a two sided business card. We would like the back to be our logo with web URL. Front should included Name, title, address, phone, fax and email address.

our address is
627 West Dorrance Blvd, Suite 308
Anaheim, CA 92718

Our logo files are attached.

Construction

```html
<!DOCTYPE html>
<html lang="en">
<head>
<meta charset="utf-8">
<title>Braxton Business Card</title>
<link rel="stylesheet" href="https://fonts.googleapis.com/css2?family=Source+Sans+3:wght@400;700&display=swap">
<style>
  :root {
    --stage: #ececec;
    --white: #ffffff;
    --brand-blue: #1c4a80;
    --slate-light: #6b6b6b;
    --slate-dark: #3e3e3e;
    --back-light: #5e5e5e;
    --back-dark: #3a3a3a;
    --ink-light: #f2f2f2;
  }
  html, body {
    margin: 0;
    padding: 0;
    width: 1200px;
    height: 402px;
    overflow: hidden;
    background: var(--stage);
    font-family: "Source Sans 3", sans-serif;
  }
  .stage { position: relative; width: 1200px; height: 402px; }
  .card {
    position: absolute;
    top: 60px;
    height: 292px;
    overflow: hidden;
    box-shadow: 0 3px 8px rgba(0,0,0,0.25);
  }
  .card-front { left: 61px; width: 509px; background: var(--white); }
  .card-back {
    left: 627px;
    width: 513px;
    background: linear-gradient(135deg, var(--back-light) 0%, var(--back-dark) 100%);
  }
  .wordmark {
    position: absolute;
    left: 0;
    right: 0;
    margin: 0;
    text-align: center;
    font-weight: 700;
    line-height: 1;
    letter-spacing: 1px;
  }
  .card-front .wordmark { top: 38px; font-size: 84px; color: var(--brand-blue); }
  .card-back .wordmark { top: 98px; font-size: 88px; color: var(--white); }

  .name-band {
    position: absolute;
    top: 160px;
    left: 0;
    width: 100%;
    height: 33px;
    background: var(--brand-blue);
    color: var(--white);
    text-align: center;
    font-size: 16px;
    line-height: 33px;
  }
  .name-band .person { font-weight: 700; }
  .contact-panel {
    position: absolute;
    top: 202px;
    left: 0;
    width: 100%;
    height: 90px;
    background: linear-gradient(90deg, var(--slate-light) 0%, var(--slate-dark) 100%);
    color: var(--ink-light);
    font-size: 13px;
  }
  .contact-col { position: absolute; top: 15px; line-height: 17px; }
  .contact-col.phones { right: 270px; }
  .contact-col.online { left: 250px; }
  .contact-line { display: flex; align-items: center; gap: 5px; white-space: nowrap; }
  .contact-col.phones .contact-line { justify-content: flex-end; }
  .contact-line svg { width: 9px; height: 9px; fill: var(--ink-light); flex: none; }
  .contact-divider {
    position: absolute;
    top: 16px;
    left: 244px;
    width: 1px;
    height: 34px;
    background: var(--ink-light);
  }
  .address {
    position: absolute;
    top: 59px;
    left: 0;
    width: 100%;
    text-align: center;
    font-size: 13px;
  }
</style>
</head>
<body>
<div class="stage">

  <section class="card card-front" aria-label="Business card front">
    <p class="wordmark">BRAXTON</p>

    <div class="name-band"><span class="person">Your Name,</span> Title</div>

    <div class="contact-panel">
      <div class="contact-col phones">
        <div class="contact-line">
          <svg viewBox="0 0 10 10" aria-hidden="true"><path d="M2 0.5 L3.6 0.5 L4.2 3 L3 3.8 C3.6 5.2 4.8 6.4 6.2 7 L7 5.8 L9.5 6.4 L9.5 8 C9.5 9 8.8 9.5 8 9.5 C4 9.2 0.8 6 0.5 2 C0.5 1.2 1 0.5 2 0.5 Z"/></svg>
          <span>01-234-5678</span>
        </div>
        <div class="contact-line">
          <svg viewBox="0 0 10 10" aria-hidden="true"><rect x="2.5" y="0.5" width="5" height="3"/><rect x="0.5" y="3.5" width="9" height="4" rx="1"/><rect x="2.5" y="6.5" width="5" height="3"/></svg>
          <span>01-234-5678</span>
        </div>
      </div>
      <div class="contact-divider"></div>
      <div class="contact-col online">
        <div class="contact-line">
          <svg viewBox="0 0 10 10" aria-hidden="true"><rect x="0.5" y="2" width="9" height="6"/><path d="M0.5 2 L5 5.5 L9.5 2" fill="none" stroke="#555" stroke-width="0.8"/></svg>
          <span>info@braxtonbuild.com</span>
        </div>
        <div class="contact-line">
          <svg viewBox="0 0 10 10" aria-hidden="true"><circle cx="5" cy="5" r="4.5"/><path d="M0.5 5 H9.5 M5 0.5 C3 3 3 7 5 9.5 M5 0.5 C7 3 7 7 5 9.5" fill="none" stroke="#555" stroke-width="0.7"/></svg>
          <span>www.braxtonbuild.com</span>
        </div>
      </div>
      <div class="address">627 West Dorrance Blvd, Suite 308, Anaheim, CA&nbsp; 92718</div>
    </div>
  </section>

  <section class="card card-back" aria-label="Business card back">
    <p class="wordmark">BRAXTON</p>
  </section>

</div>
</body>
</html>
```